Craft Brewery Beer Can Label in Alaska

Design a 16oz can label for a craft brewery.

We are making a can design that can be used for our 6 normal beers. Our desire is to have a standard design but one major element have the color change on each beer type. We included examples of how this works for others.

Elements we general like in designs - mountain scenes, waterfalls, topo map lines, hops. None/all are not required in a design but gives starting options. We are on the ocean in a glacier fjord so think mountains, glaciers and water.

Requirements
Must have
• Company Logo – provided
Bellvane Seal Logo – provided
Saltmoor Brewers Logo – provided

Alcohol warning text -

GOVERNMENT WARNING: (1) According to the Surgeon General, women should not drink alcoholic beverages during pregnancy because of the risk of birth defects. (2) Consumption of alcoholic beverages impairs your ability to drive a car or operate machinery, and may cause health problems.

Beer Name – Gullrock Pilsner
ABV – 4.9% ABV
Size – 16 FL OZ
Nice to have
• Elements we general like in designs - mountain scenes, waterfalls, topo map lines, hops. None/all are not required in a design but gives starting options. We are on the ocean in a glacier fjord so think mountains, glaciers and water.

```html
<!DOCTYPE html>
<html lang="en">
<head>
<meta charset="utf-8">
<title>Gullrock Pilsner – Can Label Colourways</title>
<link href="https://fonts.googleapis.com/css2?family=Barlow+Semi+Condensed:wght@600;700&display=swap" rel="stylesheet">
<style>
  :root {
    --stage: #d9d9d9;
    --ink: #141414;
    --white: #ffffff;
    --gold: #f2c318;
    --red: #d8232a;
    --red-deep: #9e1217;
    --green: #2f8a2b;
    --green-light: #6cd23a;
    --yellow: #f8d81c;
    --yellow-deep: #efc40e;
    --teal: #1f5c5c;
    --teal-light: #3fa39a;
    --orange: #f07a1a;
    --paper: #f6f6f4;
  }
  * { box-sizing: border-box; margin: 0; padding: 0; }
  html, body { width: 1200px; height: 874px; overflow: hidden; }
  body {
    background: var(--stage);
    font-family: "Barlow Semi Condensed", "Arial Narrow", sans-serif;
    display: flex;
    align-items: center;
    justify-content: center;
    gap: 30px;
  }
  .label {
    position: relative;
    width: 360px;
    height: 720px;
    overflow: hidden;
    display: flex;
    flex-direction: column;
    align-items: center;
    padding-top: 70px;
    background: var(--label-bg);
    color: var(--label-ink);
  }
  .label--red { --label-bg: linear-gradient(180deg, var(--red-deep), var(--red)); --label-ink: var(--white); --accent: var(--gold); --hills: var(--teal); --hills-light: var(--teal-light); --sun: var(--gold); --tag: var(--red); }
  .label--white { --label-bg: var(--paper); --label-ink: var(--ink); --accent: var(--green); --hills: var(--green); --hills-light: var(--green-light); --sun: var(--gold); --tag: var(--green); }
  .label--yellow { --label-bg: linear-gradient(180deg, var(--yellow-deep), var(--yellow)); --label-ink: var(--teal); --accent: var(--teal); --hills: var(--teal); --hills-light: var(--teal-light); --sun: var(--orange); --tag: var(--teal); }
  .label--yellow .beer-name__lead { color: var(--orange); }

  .brand { display: flex; flex-direction: column; align-items: center; }
  .brand__mark { width: 22px; height: 22px; border-radius: 50%; background: var(--accent); margin-bottom: 10px; }
  .label--white .brand__mark, .label--white .brand__name { color: var(--green); }
  .brand__name { font-size: 38px; font-weight: 700; letter-spacing: 1px; line-height: 1; color: inherit; }
  .brand__sub { font-size: 15px; font-weight: 700; letter-spacing: 9px; margin-top: 4px; padding-left: 9px; }
  .label--red .brand__name, .label--red .brand__sub { color: var(--white); }
  .label--white .brand__sub { color: var(--green); }

  .beer-name { margin-top: 40px; text-align: center; line-height: 0.9; }
  .beer-name__lead { display: block; font-size: 48px; font-weight: 700; }
  .beer-name__style { display: block; font-size: 92px; font-weight: 700; color: var(--accent); letter-spacing: 1px; }
  .label--red .beer-name__style { color: var(--gold); }

  .tagline { display: flex; align-items: center; gap: 14px; margin-top: 22px; color: var(--ink); }
  .tagline__text { font-size: 24px; font-weight: 700; letter-spacing: 1px; }
  .tagline svg { width: 48px; height: 18px; }
  .tagline polygon { fill: var(--gold); }
  .label--yellow .tagline polygon { fill: var(--orange); }

  .scene {
    position: absolute;
    left: 0; right: 0; bottom: 0;
    height: 300px;
    background:
      radial-gradient(circle at 50% 34%, var(--sun) 0 42px, transparent 43px),
      linear-gradient(180deg, transparent 0 10%, var(--hills-light) 45%, var(--hills) 100%);
  }
  .stat {
    position: absolute;
    bottom: 64px;
    padding: 5px 12px;
    font-size: 19px;
    font-weight: 700;
    color: var(--white);
    background: var(--tag);
  }
  .stat--abv { left: 0; }
  .stat--size { right: 0; }
</style>
</head>
<body>

  <section class="label label--red">
    <div class="brand">
      <span class="brand__mark"></span>
      <span class="brand__name">HARROWFJORD</span>
      <span class="brand__sub">BREWING</span>
    </div>
    <h1 class="beer-name">
      <span class="beer-name__lead">GULLROCK</span>
      <span class="beer-name__style">PILSNER</span>
    </h1>
    <div class="tagline">
      <svg viewBox="0 0 48 18"><polygon points="0,9 48,0 48,18"/></svg>
      <span class="tagline__text">ALASKA BEER</span>
      <svg viewBox="0 0 48 18"><polygon points="0,0 48,9 0,18"/></svg>
    </div>
    <div class="scene" role="img" aria-label="Line-drawn fjord mountains with a rising sun"></div>
    <span class="stat stat--abv">4.9% ABV</span>
    <span class="stat stat--size">16 FL OZ</span>
  </section>

  <section class="label label--white">
    <div class="brand">
      <span class="brand__mark"></span>
      <span class="brand__name">HARROWFJORD</span>
      <span class="brand__sub">BREWING</span>
    </div>
    <h1 class="beer-name">
      <span class="beer-name__lead">GULLROCK</span>
      <span class="beer-name__style">PILSNER</span>
    </h1>
    <div class="tagline">
      <svg viewBox="0 0 48 18"><polygon points="0,9 48,0 48,18"/></svg>
      <span class="tagline__text">ALASKA BEER</span>
      <svg viewBox="0 0 48 18"><polygon points="0,0 48,9 0,18"/></svg>
    </div>
    <div class="scene" role="img" aria-label="Line-drawn fjord mountains with a rising sun"></div>
    <span class="stat stat--abv">4.9% ABV</span>
    <span class="stat stat--size">16 FL OZ</span>
  </section>

  <section class="label label--yellow">
    <div class="brand">
      <span class="brand__mark"></span>
      <span class="brand__name">HARROWFJORD</span>
      <span class="brand__sub">BREWING</span>
    </div>
    <h1 class="beer-name">
      <span class="beer-name__lead">GULLROCK</span>
      <span class="beer-name__style">PILSNER</span>
    </h1>
    <div class="tagline">
      <svg viewBox="0 0 48 18"><polygon points="0,9 48,0 48,18"/></svg>
      <span class="tagline__text">ALASKA BEER</span>
      <svg viewBox="0 0 48 18"><polygon points="0,0 48,9 0,18"/></svg>
    </div>
    <div class="scene" role="img" aria-label="Line-drawn fjord mountains with a setting orange sun"></div>
    <span class="stat stat--abv">4.9% ABV</span>
    <span class="stat stat--size">16 FL OZ</span>
  </section>

</body>
</html>
```